Business card design Needed for new logo / Construction business, home extensions and new builds

We need a business card design using our new logo files which i will attach to this project :)

We are a small construction business specialising in home extensions, new builds and property development. We are very ambitious and would appreciate professional and elegant designs for our new business card.

Very serious about using the services on MakerQuarry and recently acquired our new logo from here :)

Please get involved, i will feedback when i can as i am very busy but can respond daily, thanks

Target Market(s)

People that want to build onto their houses, new building developments or adding too their existing property

Industry/Entity Type

Construction

Contact Information for Business Card

Renwick Tolliver Construction, Lionel Ashby (Managing Director), Tel 07822254961, email - info@renwick-tolliver, www.renwick-tolliver.co.uk

Colors

Designer to choose colors to be used in the design.

Requirements
Must have
• I like a deep grey on the back please. A lot of you have provided black from and back, try mixing things up a little. The black looks cool 😎 Thanks

```html
<!DOCTYPE html>
<html lang="en">
<head>
<meta charset="utf-8">
<title>Renwick Tolliver Construction – Business Card</title>
<link rel="stylesheet" href="https://fonts.googleapis.com/css2?family=Cinzel:wght@400;600&family=Lato:wght@400;700&display=swap">
<style>
  :root {
    --backdrop: #2b2b2c;
    --card-white: #ffffff;
    --panel-black: #1d1d1e;
    --gold-light: #f8d98c;
    --gold-mid: #e0ad45;
    --gold-deep: #bf8416;
    --silver: #c9cacc;
    --ink: #141414;
  }
  * { box-sizing: border-box; margin: 0; padding: 0; }
  html, body { width: 1200px; height: 875px; overflow: hidden; }
  body {
    background: var(--backdrop);
    display: flex;
    align-items: center;
    justify-content: center;
    gap: 60px;
    font-family: "Lato", sans-serif;
  }
  .card {
    position: relative;
    width: 520px;
    height: 297px;
    border-radius: 18px;
    overflow: hidden;
    box-shadow: 0 20px 40px rgba(0,0,0,.45);
  }
  /* Front */
  .card-front {
    background: var(--card-white);
    display: flex;
    align-items: center;
    justify-content: center;
  }
  .front-brand {
    display: flex;
    align-items: center;
    gap: 14px;
  }
  .brand-square {
    width: 18px; height: 18px;
    background: var(--gold-deep);
  }
  .brand-name {
    font-family: "Cinzel", serif;
    font-weight: 600;
    font-size: 26px;
    line-height: 1.25;
    letter-spacing: 1px;
    color: var(--gold-deep);
    text-align: center;
  }
  /* Back */
  .card-back {
    background: linear-gradient(120deg, var(--gold-deep) 0%, var(--gold-light) 30%, var(--gold-mid) 58%, var(--gold-deep) 78%, var(--gold-mid) 100%);
  }
  .back-panel { position: absolute; inset: 0; width: 520px; height: 297px; }
  .back-brand {
    position: absolute;
    right: 28px;
    top: 64px;
    width: 170px;
    font-family: "Cinzel", serif;
    font-weight: 600;
    font-size: 17px;
    line-height: 1.3;
    color: var(--gold-mid);
    text-align: center;
  }
  .contact {
    position: absolute;
    left: 38px;
    top: 100px;
    color: var(--ink);
  }
  .contact-name {
    font-family: "Cinzel", serif;
    font-size: 23px;
    font-weight: 400;
    letter-spacing: .5px;
    line-height: 1;
  }
  .contact-role { font-weight: 700; font-size: 13px; margin-top: 3px; }
  .contact-address { margin-top: 16px; font-size: 12px; line-height: 1.35; }
  .contact-address strong { font-weight: 700; }
  .contact-lines { margin-top: 14px; list-style: none; font-size: 12px; line-height: 1.5; }
  .contact-lines li { display: flex; align-items: center; gap: 8px; }
  .contact-lines svg { width: 11px; height: 11px; fill: var(--ink); }
</style>
</head>
<body>
  <section class="card card-front">
    <div class="front-brand">
      <span class="brand-square"></span>
      <p class="brand-name">Renwick Tolliver<br>Construction</p>
    </div>
  </section>

  <section class="card card-back">
    <svg class="back-panel" viewBox="0 0 520 297" aria-hidden="true">
      <path d="M 322 0 L 304 150 Q 299 196 346 204 L 520 236 L 520 0 Z" fill="none" stroke="var(--silver)" stroke-width="10"/>
      <path d="M 322 0 L 304 150 Q 299 196 346 204 L 520 236 L 520 0 Z" fill="var(--panel-black)"/>
    </svg>
    <p class="back-brand">Renwick Tolliver Construction</p>

    <div class="contact">
      <h1 class="contact-name">Lionel Ashby</h1>
      <p class="contact-role">Managing Director</p>
      <p class="contact-address"><strong>Renwick Tolliver Construction</strong><br>Your Address, City<br>State, Zip 1235</p>
      <ul class="contact-lines">
        <li><svg viewBox="0 0 24 24"><path d="M6.6 10.8a15.1 15.1 0 0 0 6.6 6.6l2.2-2.2c.3-.3.7-.4 1-.2 1.1.4 2.3.6 3.6.6.6 0 1 .4 1 1V20c0 .6-.4 1-1 1A17 17 0 0 1 3 4c0-.6.4-1 1-1h3.5c.6 0 1 .4 1 1 0 1.3.2 2.5.6 3.6.1.3 0 .7-.2 1z"/></svg>07822254961</li>
        <li><svg viewBox="0 0 24 24"><path d="M2 5h20v14H2z M2 5l10 8 10-8" fill="none" stroke="#141414" stroke-width="2"/><path d="M2 5h20l-10 8z"/></svg>info@renwick-tolliver.co.uk</li>
        <li><svg viewBox="0 0 24 24"><circle cx="12" cy="12" r="10" fill="none" stroke="#141414" stroke-width="2"/><path d="M2 12h20M12 2c3 3 3 17 0 20M12 2c-3 3-3 17 0 20" fill="none" stroke="#141414" stroke-width="1.6"/></svg>renwick-tolliver.co.uk</li>
      </ul>
    </div>
  </section>
</body>
</html>
```